Animal Eye Clinic needs a Business card

We are a new veterinary ophthalmology practice (Ridgeline Pet Vision Care) and we need a business card designed. We only see animal eyes - we are not a regular veterinary clinic. We already have a logo. We are looking for a professional, good looking business card to hand out to our clients. We are looking for something simple but professional and contemporary. Our logo is likely the only picture/graphic that needs to be on the card.
Updates

Contact Information for Business Card

Delia Vossman, BSc, DVM, MSc, DipACVO
Veterinary Ophthalmologist

Phone: 250.418.3927
Email: ridgelinepetvisioncare@mailbox-example.net
Website: ridgelinepetvisioncare-example.net
Address: 1874 Thornbury Rd
Kelowna, BC, V1X 4M9

Colors

Designer to choose colors to be used in the design.

Requirements
Must have
• Our logo (attached)

```html
<!DOCTYPE html>
<html lang="en">
<head>
<meta charset="utf-8">
<title>Ridgeline Pet Vision Care – Business Card</title>
<link rel="stylesheet" href="https://fonts.googleapis.com/css2?family=Crimson+Text:wght@600&family=Lato:wght@300;400&display=swap">
<style>
  :root {
    --backdrop: #1d1d1d;
    --card-front: #5b5b5b;
    --card-back: #f3f3f1;
    --teal: #1a8b97;
    --ink: #2e2e2e;
    --ink-soft: #4a4a4a;
    --white: #f2f2f2;
    --slate: #5f5f62;
  }
  * { box-sizing: border-box; margin: 0; padding: 0; }
  html, body { width: 1200px; height: 1200px; overflow: hidden; }
  body {
    background: var(--backdrop);
    font-family: "Lato", Arial, sans-serif;
    position: relative;
  }
  .card {
    position: absolute;
    top: 455px;
    width: 548px;
    height: 312px;
    overflow: hidden;
  }
  .card--front { left: 37px; background: var(--card-front); }
  .card--back  { left: 623px; background: var(--card-back); }

  /* Front */
  .brand {
    position: absolute;
    left: 92px;
    top: 128px;
    display: flex;
    align-items: center;
    gap: 14px;
    color: var(--white);
  }
  .brand__dot {
    width: 40px; height: 40px;
    border-radius: 50%;
    background: var(--white);
  }
  .brand__name {
    font-weight: 400;
    font-size: 19px;
    letter-spacing: 0.06em;
    line-height: 1.2;
    text-transform: uppercase;
  }

  /* Back */
  .artwork {
    position: absolute;
    left: 0;
    top: 50px;
    width: 135px;
    height: 200px;
    background: linear-gradient(160deg, var(--teal) 0%, var(--teal) 55%, var(--slate) 100%);
    border-radius: 0 60px 24px 0;
  }
  .person {
    position: absolute;
    left: 196px;
    top: 46px;
  }
  .person__line { display: flex; align-items: baseline; gap: 9px; white-space: nowrap; }
  .person__name {
    font-family: "Crimson Text", Georgia, serif;
    font-weight: 600;
    font-size: 28px;
    color: var(--teal);
    letter-spacing: 0.01em;
  }
  .person__creds {
    font-size: 9px;
    letter-spacing: 0.2em;
    color: var(--ink-soft);
  }
  .person__title {
    margin-top: 3px;
    font-size: 14px;
    letter-spacing: 0.08em;
    color: var(--ink);
  }
  .contact {
    position: absolute;
    left: 192px;
    top: 200px;
    border-collapse: collapse;
  }
  .contact th {
    text-align: left;
    font-weight: 400;
    font-size: 14px;
    color: var(--teal);
    padding: 0 18px 4px 0;
    width: 52px;
  }
  .contact td {
    font-weight: 300;
    font-size: 13.5px;
    color: var(--ink-soft);
    padding-bottom: 4px;
    white-space: nowrap;
  }
</style>
</head>
<body>
  <section class="card card--front" aria-label="Card front">
    <div class="brand">
      <span class="brand__dot" aria-hidden="true"></span>
      <span class="brand__name">Ridgeline<br>Pet Vision Care</span>
    </div>
  </section>

  <section class="card card--back" aria-label="Card back">
    <div class="artwork" role="img" aria-label="Artwork area: horse, dog and cat silhouettes in teal and grey"></div>
    <div class="person">
      <div class="person__line">
        <span class="person__name">Delia Vossman</span>
        <span class="person__creds">BSc, DVM, MSc, DipACVO</span>
      </div>
      <p class="person__title">Veterinary Ophthalmologist</p>
    </div>
    <table class="contact">
      <tr><th>P:</th><td>250.418.3927</td></tr>
      <tr><th>E:</th><td>ridgelinepetvisioncare@mailbox-example.net</td></tr>
      <tr><th>W:</th><td>ridgelinepetvisioncare-example.net</td></tr>
      <tr><th>Add:</th><td>1874 Thornbury Rd Kelowna, BC, V1X 4M9</td></tr>
    </table>
  </section>
</body>
</html>
```